New Business Card Design Project

Use the flyer uploaded and website www.brightoakbuilders.com for inspiration.
List Our Services on Backside of business cards
Marcus Delling
Harborline Builders Inc.
Licensed General Contractors
858-471-6093

Contact Information for Business Card

Use the flyer uploaded and website www.brightoakbuilders.com for inspiration. List Our Services on Backside of business cards Marcus Delling Harborline Builders Inc. Licensed General Contractors 858-471-6093

```html
<!DOCTYPE html>
<html lang="en">
<head>
<meta charset="utf-8">
<title>Harborline Builders – Business Card</title>
<link rel="stylesheet" href="https://fonts.googleapis.com/css2?family=Cinzel:wght@400;600&family=Poppins:wght@400&display=swap">
<style>
  :root {
    --backdrop: #adadad;
    --card: #121212;
    --ink: #ffffff;
    --accent: #3a86c8;
    --alert: #e3141f;
    --rule: #4a4a4a;
  }
  * { margin: 0; padding: 0; box-sizing: border-box; }
  html, body { width: 1093px; height: 1200px; overflow: hidden; }
  body { background: var(--backdrop); position: relative; font-family: 'Poppins', sans-serif; }

  .card {
    position: absolute; left: 264px; width: 580px; height: 358px;
    background: var(--card); border-radius: 30px; color: var(--ink);
  }
  .card--front { top: 226px; }
  .card--back { top: 621px; }

  .brand-name {
    position: absolute; transform: translateX(-50%);
    font-family: 'Cinzel', serif; font-weight: 400;
    letter-spacing: 0.3px; white-space: nowrap; color: var(--ink);
  }
  .card--front .brand-name { left: 148px; top: 196px; font-size: 18.5px; }
  .card--back .brand-name { left: 131px; top: 190px; font-size: 16px; }

  .divider {
    position: absolute; width: 1px;
    background: linear-gradient(to bottom, transparent, var(--rule) 25%, var(--rule) 75%, transparent);
  }
  .card--front .divider { left: 289px; top: 71px; height: 211px; }
  .card--back .divider { left: 253px; top: 82px; height: 205px; }

  .person-name {
    position: absolute; left: 313px; top: 110px;
    font-family: 'Cinzel', serif; font-weight: 600; font-size: 22px;
    color: var(--accent); letter-spacing: 0.3px; white-space: nowrap;
  }
  .contact-list { position: absolute; left: 311px; top: 172px; list-style: none; }
  .contact-list li {
    display: flex; align-items: center; height: 21px;
    font-size: 17px; line-height: 21px; white-space: nowrap;
  }
  .contact-list svg { width: 15px; height: 15px; margin-right: 10px; flex: none; }

  .tagline {
    position: absolute; left: 0; right: 0; top: 295px; text-align: center;
    font-size: 17px; color: var(--alert); white-space: nowrap;
  }
  .tagline .sep { color: var(--accent); }

  .service-list { position: absolute; left: 276px; top: 86px; list-style: none; }
  .service-list li {
    position: relative; padding-left: 13px; height: 22px; line-height: 22px;
    font-size: 17.5px; white-space: nowrap;
  }
  .service-list li::before {
    content: ""; position: absolute; left: 0; top: 8px;
    width: 6px; height: 6px; border-radius: 50%; background: var(--accent);
  }
</style>
</head>
<body>

<section class="card card--front">
  <div class="brand-name">HARBORLINE BUILDERS</div>
  <div class="divider"></div>
  <div class="person-name">MARCUS DELLING</div>
  <ul class="contact-list">
    <li>
      <svg viewBox="0 0 24 24" fill="none" stroke="#3a86c8" stroke-width="2" stroke-linecap="round" stroke-linejoin="round"><path d="M22 16.9v3a2 2 0 0 1-2.2 2 19.8 19.8 0 0 1-8.6-3.1 19.5 19.5 0 0 1-6-6A19.8 19.8 0 0 1 2.1 4.2 2 2 0 0 1 4.1 2h3a2 2 0 0 1 2 1.7c.1 1 .4 1.9.7 2.8a2 2 0 0 1-.5 2.1L8 9.9a16 16 0 0 0 6 6l1.3-1.3a2 2 0 0 1 2.1-.4c.9.3 1.8.6 2.8.7a2 2 0 0 1 1.7 2z"/><path d="M15 2a7 7 0 0 1 7 7M15 6a3 3 0 0 1 3 3"/></svg>
      858-471-6093
    </li>
    <li>
      <svg viewBox="0 0 24 24"><rect x="1" y="4" width="22" height="16" fill="#3a86c8"/><path d="M1 4l11 9 11-9M1 20l8-8M23 20l-8-8" fill="none" stroke="#121212" stroke-width="1.6"/></svg>
      info@brightoak.com
    </li>
    <li>
      <svg viewBox="0 0 24 24" fill="none" stroke="#3a86c8" stroke-width="1.8"><circle cx="12" cy="12" r="10"/><ellipse cx="12" cy="12" rx="4.5" ry="10"/><path d="M2 12h20M4 7h16M4 17h16"/></svg>
      BrightOakBuilders.com
    </li>
  </ul>
  <p class="tagline">Harborline Builders Inc. <span class="sep">|</span> Licensed General Contractors</p>
</section>

<section class="card card--back">
  <div class="brand-name">HARBORLINE BUILDERS</div>
  <div class="divider"></div>
  <ul class="service-list">
    <li>Remodel: Kitchen &amp; Bath</li>
    <li>Painting: Interior &amp; Exterior</li>
    <li>Flooring: Carpet, Vinyl, Wood</li>
    <li>Window &amp; Door Replacement</li>
    <li>Plumbing: Repairs &amp; Upgrades</li>
    <li>Energy-Efficient Upgrades</li>
    <li>Deck &amp; Patio Construction</li>
    <li>Water &amp; Mold Damage</li>
    <li>Garage Renovation</li>
  </ul>
</section>

</body>
</html>
```